Korrabel Ice Creamery tourist signage

We need to give passing tourists a snapshot of what great fun they can have visiting our brand new Ice creamery located in Timboon, 17km North of the Great Ocean Road and Famous 12 Apostles in Victoria Australia. So the sign needs to be more than directional, need to be enticing. needs to be designed in a manner that project quality. ( keep in mind cars travelling at 80km don't have a lot of time to read too much)
Size is 2.2metres wide by 1.4 meters high
This sign needs to be succinct. Needs to convey fun and a little indulgence but not in a 'tacky' or 'cheap' way.
Needs to offer indulgent imagery of course, our logo too and direction.

Target Market(s)

Tourists, domestic and internationals

Industry/Entity Type

Tourism

Font styles to use
Other font styles liked:
• sacred cow

Colors
add136
fdf3f8
b8a6cd
fabb94
fcca95
85acd3
fbf289

Requirements
Must have
• Convey fun, whimsy indulgence and value ( keeping in mind we need to entice these people a further 17km up the road!)
Nice to have
• White space and clear imagery with
Should not have
• Bold bling colours, be busy looking and cheap looking, needs to convey quality .

```html
<!DOCTYPE html>
<html lang="en">
<head>
<meta charset="utf-8">
<title>Korrabel Ice Creamery – Tourist Sign</title>
<link rel="stylesheet" href="https://fonts.googleapis.com/css2?family=Fredoka:wght@600&display=swap">
<style>
  :root {
    --stage: #e6e6e6;
    --panel: #f3f3f3;
    --lime: #a8cf38;
    --butter: #f6f08f;
    --ink: #2b2b2b;
    --grape: #8a1fd0;
    --grape-light: #b13cff;
    --grape-deep: #8c00e8;
  }
  html, body {
    margin: 0;
    padding: 0;
    width: 1200px;
    height: 886px;
    overflow: hidden;
    background: var(--stage);
  }
  .sign {
    position: absolute;
    left: 0;
    top: 62px;
    width: 1200px;
    height: 762px;
    display: block;
  }
  .panel { fill: var(--panel); }
  .band-lime { fill: var(--lime); }
  .band-butter { fill: var(--butter); }
  .brand-name,
  .brand-tagline {
    font-family: "Fredoka", sans-serif;
    font-weight: 600;
    fill: var(--ink);
  }
  .brand-name { font-size: 82px; letter-spacing: 4px; }
  .brand-tagline { font-size: 40px; letter-spacing: 2px; }
  .distance {
    font-family: "Fredoka", sans-serif;
    font-weight: 600;
    font-size: 84px;
    fill: var(--grape);
  }
  .chevron-back { fill: var(--grape-light); }
  .chevron-front { fill: var(--grape-deep); }
</style>
</head>
<body>
<svg class="sign" viewBox="0 0 1128 716" xmlns="http://www.w3.org/2000/svg">
  <defs>
    <linearGradient id="scoopTones" x1="0" y1="0" x2="1" y2="0.6">
      <stop offset="0" stop-color="#5a3a32"/>
      <stop offset="0.25" stop-color="#c9b7b8"/>
      <stop offset="0.42" stop-color="#f0a070"/>
      <stop offset="0.6" stop-color="#e2427e"/>
      <stop offset="0.78" stop-color="#f7cf4a"/>
      <stop offset="1" stop-color="#d82a4c"/>
    </linearGradient>
  </defs>

  <rect class="hero-photo" x="0" y="0" width="1128" height="716" fill="url(#scoopTones)"
        role="img" aria-label="Photograph of six scoops of colourful ice cream in cones with sprinkles"/>

  <path class="panel" d="M0,498 C60,530 120,552 174,562 C420,625 820,610 1128,483 L1128,716 L0,716 Z"/>
  <path class="band-butter" d="M174,560 C420,625 820,612 1128,483 L1128,450 C800,598 420,615 174,560 Z"/>
  <path class="band-lime" d="M174,558 C400,600 800,560 1128,383 L1128,453 C800,600 420,612 174,558 Z"/>

  <g class="brand">
    <text class="brand-name" x="70" y="578">KORRABEL</text>
    <text class="brand-tagline" x="334" y="642" text-anchor="middle">* ICE CREAMERY *</text>
  </g>

  <g class="direction">
    <text class="distance" x="762" y="688">17km</text>
    <polygon class="chevron-back" points="974,566 1012,566 1058,629 1012,693 974,693 1018,629"/>
    <polygon class="chevron-front" points="1018,566 1034,566 1078,629 1034,693 1018,693 1060,629"/>
  </g>
</svg>
</body>
</html>
```